Website for Architecture & Interior Design firm

We are architecture and interior design firm looking for website design, word press based, smooth, elegant and easy to use for visitors. It should be easy to navigate using a mobile phone, with the ability to change pictures easily. It is a Bilingual website, (English: left to right, Arabic: right to left). A button in the menu bar is required to change the language, At first, we expect an English version, then we will help the designer by providing Arabic translation for any part of the website. Our website main purpose is to display our works in a picture format (Portfolio) to our clients, which mainly consist of four galleries from our (Services) as follow: 1- Architecture 2- Interior Design 3- Project Management 4- Importing from Abroad - Each service will have its page, which displays projects(items) in thumbnail format with simple text, which deploys (when clicked) into Fullscreen gallery to show the items related pictures (Dark gray or black background). - Navigation buttons/arrows are required, (X) button to close the navigation. - This is a very important part, the user experience in PC/Browser mode or Mobile mode should be easy, error-free and fast. Our homepage consists of four main elements: A- Edge to edge picture (Changing in a smooth transitional way, Random pictures from our Services) with our Logo, also persistent menu bar in the top (Home | About Us | Architecture | Interior design | Project Management | Importing from Abroad) + Social media icons B- Photo tiles (Random pictures from our Services) C- Our Services in a fixed 4-tile picture (Clickable) D- Contact Section (Simple name, contact number, message form) We expect the final service should be: 1- a fully functioning website, WordPress based, ready to be used by visitors 2- full content filling, we will contact the designer and provide the material (texture, text,etc..)
Colors
Designer to choose colors to be used in the design.
Look and feel
Each slider illustrates characteristics of the customer's brand and the style your logo design should communicate.

```html
<!DOCTYPE html>
<html lang="en">
<head>
<meta charset="utf-8">
<title>Meridian Designs</title>
<link href="https://fonts.googleapis.com/css2?family=Roboto:wght@300;400;500;700;900&family=Open+Sans:wght@400;600&display=swap" rel="stylesheet">
<style>
:root{
  --navy:#1d2a44;
  --blue:#1f66b1;
  --ink:#222222;
  --white:#ffffff;
}
*{margin:0;padding:0;box-sizing:border-box}
html,body{width:1200px;height:3333px;overflow:hidden;background:var(--white)}
body{position:relative;font-family:"Roboto",Arial,sans-serif;color:var(--ink)}
.abs{position:absolute}
.hero{left:0;top:0;width:1200px;height:712px;background:linear-gradient(180deg,#3a4476 0%,#2d3460 18%,#3b2f58 34%,#6d4a6a 50%,#9a6a4e 66%,#5e4050 82%,#2c2a3c 100%)}
.hero-shade{left:0;top:0;width:1200px;height:712px;background:radial-gradient(ellipse 55% 45% at 35% 62%,rgba(240,170,90,.35),rgba(0,0,0,0) 70%),radial-gradient(ellipse 30% 60% at 72% 40%,rgba(150,120,220,.35),rgba(0,0,0,0) 70%),linear-gradient(180deg,rgba(20,20,40,.35),rgba(0,0,0,0) 30%,rgba(0,0,0,0) 70%,rgba(20,15,30,.35))}
.nav a{position:absolute;top:90px;color:var(--white);font-size:13.5px;font-weight:700;text-decoration:none;white-space:nowrap}
.nav .active{border-bottom:3px solid var(--white);padding-bottom:9px}
.brand-box{left:487px;top:0;width:233px;height:195px;background:var(--white);display:flex;flex-direction:column;align-items:center;justify-content:center;gap:10px;box-shadow:0 2px 6px rgba(0,0,0,.15)}
.brand-box .mark{width:44px;height:44px;background:var(--blue)}
.brand-box .name{color:var(--navy);font-size:16px;font-weight:400;letter-spacing:2px;text-align:center;line-height:1.35}
.social{display:flex;gap:33px}
.social span{width:14px;height:14px;border:2px solid var(--white);border-radius:50%;display:block}
.lang{left:1055px;top:32px;width:78px;height:32px;border:1px solid rgba(255,255,255,.8);color:var(--white);font-size:12px;display:flex;align-items:center;justify-content:center;gap:5px}
.hero-welcome{left:0;width:1200px;top:294px;text-align:center;color:var(--white);font-weight:300;font-size:44px}
.hero-title{left:0;width:1200px;top:350px;text-align:center;color:var(--white);font-weight:900;font-size:72px}
.btn{display:flex;align-items:center;justify-content:center;color:var(--white);font-weight:700;font-size:19px;background:var(--blue)}
.hero-btn{left:496px;top:447px;width:207px;height:51px}
.about-title{left:591px;top:798px;font-size:36px;font-weight:700;color:var(--navy)}
.bar{height:4px;background:var(--navy)}
.about-text{left:588px;top:876px;width:530px;font-family:"Open Sans",Arial,sans-serif;font-size:16.5px;line-height:27px}
.about-text p+p{margin-top:27px}
.about-btn{left:584px;top:1071px;width:186px;height:48px;font-size:18px;font-weight:500}
.section-title{left:0;width:1200px;text-align:center;font-size:36px;font-weight:700}
.tile{overflow:hidden}
.tile-label{position:absolute;left:0;right:0;color:var(--white);font-weight:700;font-size:22px;text-align:center;line-height:27px}
.tile-band{position:absolute;left:0;right:0;bottom:0;height:62px;background:rgba(40,40,40,.45)}
.pm-btn{position:absolute;left:71px;top:200px;width:152px;height:40px;border:2px solid var(--white);color:var(--white);font-size:16px;font-weight:500;display:flex;align-items:center;justify-content:center}
.contact{left:0;top:2406px;width:1200px;height:698px;background:linear-gradient(180deg,#2070ba 0%,#1d64ad 50%,#1a5aa2 80%,#2466ad 100%)}
.field{background:var(--white);color:#555;font-size:17px;padding:0 20px;display:flex;align-items:center}
.submit{left:505px;top:2944px;width:207px;height:52px;background:#1e2a3b;font-size:19px}
.foot-brand{left:171px;top:3168px;color:#1e2535;font-size:38px;font-weight:400;line-height:44px}
.foot-links a{display:block;color:var(--navy);font-size:13.5px;font-weight:700;text-decoration:none;line-height:25.5px}
.foot-social span{border-color:var(--navy)}
.foot-meta{left:876px;top:3227px;font-size:13px;color:var(--navy);line-height:26px}
</style>
</head>
<body>

<div class="abs hero" role="img" aria-label="Night aerial view of a city skyline with a lit tower"></div>
<div class="abs hero-shade"></div>
<nav class="nav">
  <a class="active" style="left:126px">ABOUT US</a>
  <a style="left:220px">ARCHITECTURE</a>
  <a style="left:350px">INTERIOR DESIGN</a>
  <a style="left:770px">PROJECT MANAGEMENT</a>
  <a style="left:958px">IMPORTING FROM ABROAD</a>
</nav>
<div class="abs brand-box">
  <span class="mark"></span>
  <div class="name">MERIDIAN<br>DESIGN &amp; PROJECT<br>MANAGEMENT</div>
</div>
<div class="abs social" style="left:868px;top:41px"><span></span><span></span><span></span><span></span></div>
<div class="abs lang">ENG
  <svg width="14" height="9" viewBox="0 0 14 9"><path d="M1 1l6 6 6-6" fill="none" stroke="#fff" stroke-width="2"/></svg>
</div>
<svg class="abs" style="left:88px;top:342px" width="30" height="60" viewBox="0 0 30 60"><path d="M28 2L3 30l25 28" fill="none" stroke="rgba(255,255,255,.7)" stroke-width="2"/></svg>
<svg class="abs" style="left:1110px;top:342px" width="30" height="60" viewBox="0 0 30 60"><path d="M2 2l25 28L2 58" fill="none" stroke="rgba(255,255,255,.7)" stroke-width="2"/></svg>
<div class="abs hero-welcome">WELCOME TO</div>
<div class="abs hero-title">MERIDIAN DESIGNS</div>
<div class="abs btn hero-btn">GET STARTED</div>
<svg class="abs" style="left:228px;top:655px" width="200" height="58" viewBox="0 0 200 58"><polygon points="0,58 100,0 200,58" fill="#fff"/></svg>

<svg class="abs" style="left:124px;top:727px" width="406" height="465" viewBox="0 0 406 465" role="img" aria-label="Architect's hands sketching plans on a desk with a coffee cup">
  <defs><linearGradient id="hexFill" x1="0" y1="0" x2="1" y2="1"><stop offset="0" stop-color="#d9c79a"/><stop offset=".3" stop-color="#ebe8e2"/><stop offset=".65" stop-color="#c6ccd2"/><stop offset="1" stop-color="#6f93b6"/></linearGradient></defs>
  <polygon points="203,0 406,118 406,348 203,465 0,348 0,118" fill="url(#hexFill)"/>
</svg>
<h2 class="abs about-title">ABOUT US</h2>
<div class="abs bar" style="left:591px;top:851px;width:80px"></div>
<div class="abs about-text">
  <p>Fusce tellus Sed metus augue convallis et vehicula ut pulvinar eu ante Integer orci tellus tristique vitae consequat nec</p>
  <p>Aorta vel lectus Nulla sit amet enim Proin dui lectus cursus eu mattis laoreet viverra sit amet quam Curabitur vel dolor ultrices ipsum dictum tristique Praesent vitae lacus Ut velit e</p>
</div>
<div class="abs btn about-btn">LEARN MORE</div>

<h2 class="abs section-title" style="top:1270px;color:var(--navy)">OUR SERVICES</h2>
<div class="abs bar" style="left:558px;top:1321px;width:80px"></div>

<div class="abs tile" style="left:0;top:1371px;width:296px;height:292px;background:linear-gradient(120deg,#c9c4bc 0%,#9a948c 35%,#5d86c4 65%,#2f6fc4 100%)" role="img" aria-label="Modern building facade with a sculpted lattice">
  <div class="tile-band"></div><div class="tile-label" style="bottom:24px">ARCHITECTURE</div>
</div>
<div class="abs tile" style="left:303px;top:1371px;width:293px;height:292px;background:linear-gradient(180deg,#8a7442 0%,#3a2e22 35%,#2a241c 55%,#9a8660 85%,#6a5a40 100%)" role="img" aria-label="Ornate mosque interior with striped arches">
  <div class="tile-band"></div><div class="tile-label" style="bottom:22px">INTERIOR DESIGN</div>
</div>
<div class="abs tile" style="left:605px;top:1353px;width:293px;height:326px;background:linear-gradient(160deg,#4a92d6,#2a6fba 55%,#2262aa)" role="img" aria-label="Engineers reviewing plans at a construction site, blue tint">
  <div class="tile-label" style="top:122px">PROJECT<br>MANAGEMENT</div>
  <div class="pm-btn">CLICK HERE</div>
</div>
<div class="abs tile" style="left:907px;top:1371px;width:293px;height:292px;background:linear-gradient(180deg,#6a6a82 0%,#a88272 35%,#7a5a48 52%,#3e3a36 72%,#2c2c2c 100%)" role="img" aria-label="Cargo port with cranes at dusk">
  <div class="tile-label" style="bottom:20px">IMPORTING FROM<br>ABROAD</div>
</div>

<h2 class="abs section-title" style="top:1765px;color:var(--blue)">OUR GALLERY</h2>
<div class="abs bar" style="left:547px;top:1816px;width:80px"></div>
<div class="abs" style="left:0;top:1841px;width:388px;height:277px;background:linear-gradient(180deg,#c4d0dc 0%,#d6c2a2 45%,#a39468 65%,#6a6a5e 85%,#8a8a88 100%)" role="img" aria-label="City street lined with palm trees and towers"></div>
<div class="abs" style="left:397px;top:1841px;width:396px;height:277px;background:linear-gradient(160deg,#4f86c6 0%,#7aa0c8 25%,#d9caa6 50%,#3f6a74 75%,#243c46 100%)" role="img" aria-label="Building with triangular glass facade"></div>
<div class="abs" style="left:803px;top:1841px;width:397px;height:277px;background:radial-gradient(circle at 42% 35%,#d8ecfa 0 9%,#d8cfc4 22%,#a89e94 45%,#6e6660 72%,#34302e)" role="img" aria-label="Spiral interior atrium with skylight"></div>
<div class="abs" style="left:0;top:2128px;width:388px;height:278px;background:linear-gradient(180deg,#b6d2ea 0%,#5aa0c4 35%,#2f7e98 60%,#5f7258 82%,#7a7a74 100%)" role="img" aria-label="Glass office towers along a boulevard"></div>
<div class="abs" style="left:397px;top:2128px;width:396px;height:278px;background:radial-gradient(ellipse 30% 40% at 50% 95%,#fbf1dc,rgba(0,0,0,0) 70%),linear-gradient(135deg,#f4aa52,#e67e2a 50%,#f0c48a)" role="img" aria-label="Orange arched corridor in perspective"></div>
<div class="abs" style="left:803px;top:2128px;width:397px;height:278px;background:linear-gradient(180deg,#141c48 0%,#223068 45%,#5d8450 78%,#3a5a2c 100%)" role="img" aria-label="Mosque with green dome and minaret at night"></div>

<div class="abs contact" role="img" aria-label="City skyline under a blue overlay"></div>
<h2 class="abs section-title" style="top:2468px;color:var(--white)">CONTACT US</h2>
<div class="abs bar" style="left:558px;top:2518px;width:80px;background:var(--white)"></div>
<div class="abs" style="left:0;width:1200px;top:2563px;text-align:center;color:var(--white);font-weight:500;font-size:21px">MERIDIAN DESIGNS</div>
<div class="abs" style="left:0;width:1200px;top:2591px;text-align:center;color:var(--white);font-weight:500;font-size:29px">(685) 555 0172</div>
<div class="abs field" style="left:196px;top:2665px;width:391px;height:52px">Name</div>
<div class="abs field" style="left:605px;top:2665px;width:391px;height:52px">Phone Number</div>
<div class="abs field" style="left:196px;top:2731px;width:391px;height:52px">Email address</div>
<div class="abs field" style="left:605px;top:2731px;width:391px;height:52px">Subject</div>
<div class="abs field" style="left:196px;top:2802px;width:800px;height:120px;align-items:flex-start;padding-top:16px">Message</div>
<div class="abs btn submit">SUBMIT NOW</div>

<div class="abs foot-brand">MERIDIAN<br>DESIGNS</div>
<div class="abs foot-links" style="left:421px;top:3167px"><a>HOME</a><a>ABOUT US</a><a>ARCHITECTURE</a><a>INTERIOR DESIGN</a></div>
<div class="abs foot-links" style="left:612px;top:3169px"><a>PROJECT MANAGEMENT</a><a>IMPORTING FROM ABROAD</a><a>CONTACT US</a></div>
<div class="abs social foot-social" style="left:876px;top:3173px"><span></span><span></span><span></span><span></span></div>
<div class="abs foot-meta">© 2019 Company Name<br>All right reserved &nbsp;|&nbsp; Privacy Policy</div>

</body>
</html>
```